New design for Giftwell Hub Website - landing page plus 3 carousel pages

We have a new website we want to launch for 501c3 organizations - Faith-based organizations, not for profit organizations, colleges and universities. Note - this is a design only project. We want to see designs for the landing page and the 3 other pages - Faith-based organizations, not for profit organizations, colleges and universities.
Format: We expect to create this website in Wix so requirement is to make the graphics Wix compatible
See Dossier attached for more details, 4 wireframes (1 landing page and 3 carousel pages), and brand guidelines
Please be creative and and make the visuals engaging. We do NOT want you to simply replicate what is in the wireframe. We are looking for a totally new, fresh and engaging design.
Number of Pages Required
1 page
Look and feel
Each slider illustrates characteristics of the customer's brand and the style your logo design should communicate.

```html
<!DOCTYPE html>
<html lang="en">
<head>
<meta charset="utf-8">
<title>Giftwell Hub — Non Profit Organization</title>
<link href="https://fonts.googleapis.com/css2?family=Jost:wght@400;500;600;700&family=Nunito:wght@400;600;800;900&display=swap" rel="stylesheet">
<style>
:root{
  --green:#12c785;
  --green-dark:#16925a;
  --navy:#0b1a3d;
  --sky:#4aa8e6;
  --ink:#222;
  --muted:#555;
  --white:#fff;
  --card-shadow:0 6px 18px rgba(0,0,0,.12);
}
*{box-sizing:border-box;margin:0;padding:0}
html,body{width:1200px;height:4286px;overflow:hidden}
body{position:relative;font-family:"Jost",sans-serif;color:var(--ink);background:var(--white)}
.abs{position:absolute}
.brand{display:flex;align-items:center;gap:10px;font-family:"Jost",sans-serif;font-weight:500;white-space:nowrap}
.brand-dot{border-radius:50%;border:4px solid var(--green);flex:none}
/* header */
.site-header{left:0;top:0;width:1200px;height:83px;border-top:4px solid var(--green);background:var(--white)}
.site-header .brand{position:absolute;left:68px;top:12px;font-size:30px;color:var(--navy)}
.site-header .brand-dot{width:52px;height:52px;border-color:var(--navy)}
.main-nav{position:absolute;left:335px;top:34px;display:flex;gap:45px;font-size:13px;font-weight:500;color:var(--navy)}
.main-nav .active{color:var(--green);border-bottom:2px solid var(--green);padding-bottom:8px}
.login{position:absolute;left:1000px;top:20px;width:132px;height:48px;background:var(--navy);border-radius:6px;color:#fff;font-size:13px;font-weight:600;display:flex;align-items:center;padding-left:20px;gap:26px}
.arrow-dot{width:28px;height:28px;border-radius:50%;background:#fff;display:flex;align-items:center;justify-content:center;flex:none}
/* hero */
.hero{left:0;top:83px;width:1200px;height:594px;background:linear-gradient(135deg,#3d3a2e 0%,#6b6a55 45%,#2f3a2a 100%)}
.hero h1{position:absolute;left:110px;top:135px;font-size:60px;line-height:74px;font-weight:700;color:#fff}
.hero p{position:absolute;left:111px;top:300px;font-size:17px;line-height:27px;font-weight:600;color:#fff;width:500px}
.partner{position:absolute;top:382px;background:rgba(255,255,255,.85)}
.hero-placeholder{position:absolute;left:888px;top:190px;width:170px;height:170px;border-radius:50%;background:rgba(18,199,133,.25)}
/* process */
.section-title{position:absolute;width:1200px;text-align:center;font-size:38px;font-weight:600;color:#2b2b2b}
.title-bar{position:absolute;left:570px;width:60px;height:7px;border-radius:4px;background:var(--green)}
.step-h{position:absolute;font-size:23px;font-weight:500;color:#222}
.step-p{position:absolute;width:240px;font-size:13px;line-height:22px;color:#444}
.step-p.left{text-align:right}
.node{position:absolute;width:14px;height:14px;border-radius:50%;background:var(--green)}
.diag-label{position:absolute;width:220px;text-align:center;font-size:18px;font-weight:500;line-height:28px;color:#222}
.btn-green{position:absolute;background:var(--green);border-radius:6px;color:var(--navy);font-size:13px;font-weight:500;display:flex;align-items:center;justify-content:center;gap:18px}
/* donation */
.donation{left:111px;top:1459px;width:977px;height:438px;background:var(--sky)}
.donation h2{position:absolute;left:67px;top:78px;font-size:40px;font-weight:800;color:#fff;font-family:"Nunito",sans-serif}
.donation .bar{position:absolute;left:67px;top:140px;width:78px;height:6px;background:#fff;border-radius:3px}
.donation .note{position:absolute;left:67px;top:170px;font-size:19px;color:#fff}
.donation .give{position:absolute;left:65px;top:200px;font-family:"Nunito",sans-serif;font-weight:900;font-style:italic;font-size:40px;color:#fff}
.cc-btn{position:absolute;left:68px;top:291px;width:278px;height:47px;background:var(--navy);border-radius:6px;color:#fff;font-size:13px;font-weight:600;display:flex;align-items:center;padding-left:20px;gap:14px}
.amount{position:absolute;width:99px;height:60px;background:#fff;border-radius:6px;box-shadow:0 3px 8px rgba(0,0,0,.15);display:flex;align-items:center;justify-content:center;font-size:22px;font-weight:500;color:#222;text-align:center;line-height:20px}
.amount.small{font-size:17px}
.amount.selected{background:var(--navy);color:#fff}
.pay{position:absolute;top:318px;font-size:20px;font-weight:600;color:#fff}
/* cards */
.card{position:absolute;background:#fff;box-shadow:var(--card-shadow);border-radius:4px;text-align:center}
.icon-ring{position:absolute;left:80px;top:42px;width:150px;height:150px;border-radius:50%;background:var(--navy);box-shadow:0 0 0 3px #3a6ae0 inset}
.card h3{position:absolute;width:100%;top:237px;font-size:19px;font-weight:500;color:#222}
.card .powered{position:absolute;width:100%;top:272px;font-size:18px;color:#444}
.card .brand{position:absolute;left:0;width:100%;justify-content:center;top:303px;font-size:19px;color:var(--navy)}
/* video */
.video-band{left:0;top:2501px;width:1200px;height:308px;background:var(--navy)}
.video{left:178px;top:2586px;width:842px;height:446px;border:13px solid var(--green);border-radius:30px;background:linear-gradient(160deg,#8a8b8e,#5e6067 55%,#3f4250);overflow:hidden}
.play{position:absolute;left:306px;top:180px;width:63px;height:63px;border-radius:50%;background:var(--sky);display:flex;align-items:center;justify-content:center}
.play-text{position:absolute;left:385px;top:195px;font-size:21px;color:#fff;text-decoration:underline}
/* enroll */
.enroll-sub{position:absolute;width:1200px;text-align:center;top:3206px;font-size:18px;color:#333}
.feature{position:absolute;top:3266px;width:228px;height:215px;background:#fff;box-shadow:var(--card-shadow);border-radius:4px;text-align:center}
.feature svg{margin-top:32px}
.feature h4{font-size:23px;font-weight:500;color:#222;margin-top:12px}
.feature p{font-size:12px;line-height:18px;color:#444;margin:10px 14px 0}
/* newsletter */
.news{left:112px;top:3574px;width:977px;height:381px;background:var(--green-dark);color:#fff;text-align:center}
.news h2{position:absolute;width:100%;top:50px;font-size:34px;font-weight:500;letter-spacing:.5px}
.email{position:absolute;left:253px;top:107px;width:472px;height:42px;background:#fff;border-radius:4px;display:flex;align-items:center;padding-left:18px;color:#555;font-size:14px;gap:12px}
.send{position:absolute;right:4px;top:4px;width:100px;height:34px;background:var(--navy);border-radius:6px;color:#fff;font-size:11px;font-weight:600;display:flex;align-items:center;justify-content:center;gap:14px}
.news h3{position:absolute;width:100%;top:168px;font-size:34px;font-weight:500}
.news .lead{position:absolute;width:100%;top:218px;font-size:21px}
.news .fine{position:absolute;left:110px;width:757px;top:268px;font-size:11px;line-height:22px;font-weight:500}
.consent{position:absolute;left:232px;top:315px;display:flex;align-items:center;gap:16px;font-size:11px;font-weight:500}
.check{width:18px;height:18px;background:#fff;border-radius:3px;display:flex;align-items:center;justify-content:center}
/* footer */
.site-footer{left:0;top:4040px;width:1200px;height:246px;background:var(--navy);color:#fff}
.site-footer .brand{position:absolute;left:0;width:100%;justify-content:center;top:28px;font-size:30px;color:#fff}
.site-footer .brand-dot{width:60px;height:60px;border-color:#fff}
.footer-rule{position:absolute;left:111px;width:978px;height:1px;background:rgba(255,255,255,.25)}
.footer-nav{position:absolute;left:282px;top:130px;display:flex;gap:45px;font-size:13px;font-weight:600}
.copyright{position:absolute;width:100%;top:208px;text-align:center;font-size:12px;font-weight:500}
.to-top{position:absolute;left:1132px;top:148px;width:38px;height:38px;background:#fff;border-radius:4px;display:flex;align-items:center;justify-content:center}
</style>
</head>
<body>

<header class="abs site-header">
  <div class="brand"><span class="brand-dot"></span>Giftwell Hub</div>
  <nav class="main-nav">
    <span class="active">HOME</span><span>ABOUT US</span><span>NEWSROOM</span><span>PATENTS</span><span>CLIENTS</span><span>FAQ</span><span>CONTACT</span>
  </nav>
  <div class="login">LOG IN <span class="arrow-dot"><svg width="14" height="12" viewBox="0 0 14 12"><path d="M1 6h11M8 2l4 4-4 4" stroke="#0b1a3d" stroke-width="1.8" fill="none"/></svg></span></div>
</header>

<section class="abs hero" role="img" aria-label="Photo of many hands clasped together in a circle on grass">
  <h1>NON PROFIT<br>ORGANIZATION</h1>
  <p>Aderspici atisunde omnisiste natus errorsit voluptatem accusantium doloremque laudantium meaque psaquae.</p>
  <div class="partner" style="left:112px;width:44px;height:58px;border-radius:6px"></div>
  <div class="partner" style="left:184px;width:140px;height:50px;border-radius:4px;top:388px"></div>
  <div class="partner" style="left:356px;width:84px;height:70px;border-radius:50%;top:376px"></div>
  <div class="hero-placeholder"></div>
</section>

<h2 class="section-title" style="top:753px">PROCESS</h2>
<div class="title-bar" style="top:814px"></div>

<div class="diag-label" style="left:489px;top:850px">501c3<br>ORGANIZATIONS</div>

<svg class="abs" style="left:380px;top:880px" width="440" height="280" viewBox="0 0 440 280">
  <path d="M4 4V210M4 123H160" stroke="#222" stroke-width="2" fill="none"/>
  <path d="M424 4V210M424 123H280" stroke="#222" stroke-width="2" fill="none"/>
  <polygon points="219,27 354,268 78,268" fill="#4aa8e6"/>
  <circle cx="214" cy="145" r="26" fill="none" stroke="#fff" stroke-width="5"/>
  <text x="214" y="218" text-anchor="middle" font-family="Jost, sans-serif" font-weight="500" font-size="24" fill="#fff">Giftwell Hub</text>
</svg>

<div class="node" style="left:378px;top:877px"></div>
<div class="node" style="left:378px;top:1114px"></div>
<div class="node" style="left:797px;top:877px"></div>
<div class="node" style="left:797px;top:1114px"></div>

<div class="step-h" style="left:284px;top:868px">Step 01</div>
<p class="step-p left" style="left:118px;top:908px">Kserspiciatis unde omnis iste natus error sit voluptatem accusantium doloremque laudantium, totam rem aperiam, eaque ipsa quae ab illo inventore veritatis et quasi architecto beatae vitae dicta sunt explicabo. Nemo enim ipsam .</p>
<div class="step-h" style="left:282px;top:1106px">Step 03</div>
<p class="step-p left" style="left:118px;top:1146px">Kserspiciatis unde omnis iste natus error sit voluptatem accusantium doloremque laudantium, totam rem aperiam, eaque ipsa quae ab illo inventore veritatis et quasi architecto beatae vitae dicta sunt explicabo. Nemo enim ipsam .</p>
<div class="step-h" style="left:832px;top:868px">Step 02</div>
<p class="step-p" style="left:833px;top:908px">Kserspiciatis unde omnis iste natus error sit voluptatem accusantium doloremque laudantium, totam rem aperiam, eaque ipsa quae ab illo inventore veritatis et quasi architecto beatae vitae dicta sunt explicabo. Nemo enim ipsam .</p>
<div class="step-h" style="left:832px;top:1106px">Step 04</div>
<p class="step-p" style="left:833px;top:1146px">Kserspiciatis unde omnis iste natus error sit voluptatem accusantium doloremque laudantium, totam rem aperiam, eaque ipsa quae ab illo inventore veritatis et quasi architecto beatae vitae dicta sunt explicabo. Nemo enim ipsam .</p>

<div class="diag-label" style="left:363px;top:1170px">DATA OBJECT<br>“DONOR”</div>
<div class="diag-label" style="left:598px;top:1170px">DATA EXCHANGE<br>“BUYER”</div>

<div class="btn-green" style="left:509px;top:1325px;width:182px;height:46px">DONATE DATA <span class="arrow-dot"><svg width="14" height="12" viewBox="0 0 14 12"><path d="M1 6h11M8 2l4 4-4 4" stroke="#0b1a3d" stroke-width="1.8" fill="none"/></svg></span></div>

<section class="abs donation">
  <h2>MY DONATION</h2>
  <div class="bar"></div>
  <div class="note">All donations are tax deductible</div>
  <div class="give">I want to give</div>
  <div class="cc-btn">DONATE WITH CREDIT CARD <span class="arrow-dot"><svg width="14" height="12" viewBox="0 0 14 12"><path d="M1 6h11M8 2l4 4-4 4" stroke="#0b1a3d" stroke-width="1.8" fill="none"/></svg></span></div>
  <div class="amount" style="left:503px;top:87px">$ 25</div>
  <div class="amount" style="left:624px;top:87px">$ 50</div>
  <div class="amount" style="left:749px;top:87px">$ 100</div>
  <div class="amount selected" style="left:491px;top:192px">$ 125</div>
  <div class="amount" style="left:623px;top:200px">$ 150</div>
  <div class="amount small" style="left:754px;top:197px">Other<br>Amount</div>
  <div class="pay" style="left:476px">Paycard</div>
  <div class="pay" style="left:568px">Mintcard</div>
  <div class="pay" style="left:664px">Roamcard</div>
  <div class="pay" style="left:768px">Expresso</div>
  <div class="pay" style="left:866px">Quickpay</div>
</section>

<article class="card" style="left:225px;top:1988px;width:308px;height:425px">
  <div class="icon-ring"><svg width="150" height="150" viewBox="0 0 150 150"><circle cx="75" cy="75" r="20" fill="none" stroke="#fff" stroke-width="3"/><path d="M75 35v20M75 95v20M35 75h20M95 75h20M47 47l14 14M89 89l14 14M103 47l-14 14M61 89l-14 14" stroke="#fff" stroke-width="3"/></svg></div>
  <h3>DONATE WITH CRYPTO</h3>
  <div class="powered">Powered by GWT</div>
  <div class="brand"><span class="brand-dot" style="width:34px;height:34px;border-width:3px"></span>Giftwell Hub</div>
  <div class="btn-green" style="left:80px;top:355px;width:148px;height:46px">DONATE <span class="arrow-dot"><svg width="14" height="12" viewBox="0 0 14 12"><path d="M1 6h11M8 2l4 4-4 4" stroke="#0b1a3d" stroke-width="1.8" fill="none"/></svg></span></div>
</article>

<article class="card" style="left:667px;top:1988px;width:310px;height:425px">
  <div class="icon-ring"><svg width="150" height="150" viewBox="0 0 150 150"><rect x="47" y="70" width="18" height="30" fill="none" stroke="#fff" stroke-width="3"/><rect x="66" y="70" width="18" height="30" fill="none" stroke="#fff" stroke-width="3"/><rect x="85" y="70" width="18" height="30" fill="none" stroke="#fff" stroke-width="3"/><path d="M58 60a14 14 0 0 1 34 0" fill="none" stroke="#fff" stroke-width="3"/></svg></div>
  <h3>DONATE WITH DATA</h3>
  <div class="btn-green" style="left:80px;top:355px;width:148px;height:46px">DONATE <span class="arrow-dot"><svg width="14" height="12" viewBox="0 0 14 12"><path d="M1 6h11M8 2l4 4-4 4" stroke="#0b1a3d" stroke-width="1.8" fill="none"/></svg></span></div>
</article>

<div class="abs video-band"></div>
<div class="abs video" role="img" aria-label="Video still of a group of smiling volunteers joining hands, seen from below">
  <div class="play"><svg width="20" height="22" viewBox="0 0 20 22"><polygon points="3,2 18,11 3,20" fill="#fff"/></svg></div>
  <div class="play-text">PLAY VIDEO</div>
</div>

<h2 class="section-title" style="top:3115px">WHY ENROLL!</h2>
<div class="title-bar" style="top:3178px"></div>
<p class="enroll-sub">To get full access to all the features, start by creating an account</p>

<div class="feature" style="left:206px">
  <svg width="56" height="54" viewBox="0 0 56 54"><rect x="3" y="8" width="50" height="42" rx="3" fill="none" stroke="#3a7fd8" stroke-width="3"/><path d="M3 18h50M16 2v12M40 2v12" stroke="#3a7fd8" stroke-width="3"/><g fill="#3a7fd8"><circle cx="14" cy="28" r="2.5"/><circle cx="24" cy="28" r="2.5"/><circle cx="34" cy="28" r="2.5"/><circle cx="44" cy="28" r="2.5"/><circle cx="14" cy="38" r="2.5"/><circle cx="24" cy="38" r="2.5"/><circle cx="34" cy="38" r="2.5"/><circle cx="44" cy="38" r="2.5"/></g></svg>
  <h4>Drops</h4>
  <p>Purchase NFTs that are directly sold by top Creators</p>
</div>
<div class="feature" style="left:486px">
  <svg width="58" height="54" viewBox="0 0 58 54"><path d="M4 20L10 4h38l6 16zM8 20v30h42V20M22 50V34h14v16" fill="none" stroke="#3a7fd8" stroke-width="3"/></svg>
  <h4>Marketplace</h4>
  <p>Bid on and auction off rare digital collectibles</p>
</div>
<div class="feature" style="left:765px">
  <svg width="58" height="54" viewBox="0 0 58 54"><rect x="12" y="4" width="42" height="34" rx="2" fill="none" stroke="#3a7fd8" stroke-width="3"/><path d="M4 14v34h40" fill="none" stroke="#3a7fd8" stroke-width="3"/><path d="M16 32l12-12 10 10 6-6 8 8" fill="none" stroke="#3a7fd8" stroke-width="3"/></svg>
  <h4>Drops</h4>
  <p>A digital gallery to showcase your collection</p>
</div>

<section class="abs news">
  <h2>GET NOTIFIED ABOUT NEW AMAZING PRODUCTS</h2>
  <div class="email"><svg width="16" height="12" viewBox="0 0 16 12"><rect x="1" y="1" width="14" height="10" fill="none" stroke="#333" stroke-width="1.5"/><path d="M1 1l7 6 7-6" fill="none" stroke="#333" stroke-width="1.5"/></svg>Email
    <div class="send">SEND <span class="arrow-dot" style="width:24px;height:24px"><svg width="12" height="10" viewBox="0 0 14 12"><path d="M1 6h11M8 2l4 4-4 4" stroke="#0b1a3d" stroke-width="1.8" fill="none"/></svg></span></div>
  </div>
  <h3>NEVER MISS A DROP</h3>
  <p class="lead">Subscribe for the latest news, drops and collectibles</p>
  <p class="fine">After reading the Privacy Notice, you may subscribe for our newsletter to get special offers and occasional surveys delivered to your inbox. Unsubscribe at any time by clicking on the link in the email.</p>
  <div class="consent"><span class="check"><svg width="12" height="10" viewBox="0 0 12 10"><path d="M1 5l3.5 3.5L11 1.5" stroke="#16925a" stroke-width="2" fill="none"/></svg></span>By Entering my email and subscibing I confirm and agree to the above.</div>
</section>

<footer class="abs site-footer">
  <div class="brand"><span class="brand-dot"></span>Giftwell Hub</div>
  <div class="footer-rule" style="top:113px"></div>
  <nav class="footer-nav"><span>HOME</span><span>ABOUT US</span><span>NEWSROOM</span><span>PATENTS</span><span>CLIENTS</span><span>FAQ</span><span>CONTACT</span></nav>
  <div class="footer-rule" style="top:182px"></div>
  <div class="copyright">© COPYRIGHT 2022 | ALL RIGHTS RESERVED</div>
  <div class="to-top"><svg width="12" height="22" viewBox="0 0 12 22"><path d="M6 21V2M1 7l5-5 5 5" stroke="#3a7fd8" stroke-width="1.8" fill="none"/></svg></div>
</footer>

</body>
</html>
```